Coaching landingpage/salespage need a layout

Hi!
We are two people from Sweden looking for help to design our coaching landingpage/salespage.

What about:
We need a nice modern timeless appealing Photoshop layout (landingpage) for our coaching page where we coach people to “how to get a richer lifestyle”.

Style of page:
We want the site to reflect seriousness but still harmonic. We would like somewhat colorful and (but not too crazy). After all, we are coaching about investments and private economy.
Responsive layout – consider stacking order when scaling down window width. Fullpage-design where content areas are 960 grid/max-width.

----------------------------------------------------------------------------
Content on page:
*Headersection – Logo and header image with the two coaches together and space for later on adding a video.

*On the landingpage the customers can read up on what we mean by a richer lifestyle (use dummy text). We show our Vardagskompassen (= Lifestyle matrix) and a little description about that. If the customers want to know more, they can click "read more (or a symbolic icon that relates to read more)" to expand a hidden div (section) where they can read more about Vardagskompassen. They can also minimize the section.

*3-4 Unique selling points “Four reasons why choose coaching” with nice designed number-icons and some place for text.

*The customer should also be able to read something about what happens during a typical coaching session, some bullets that summarize it (use dummy text) and a couple of headlines, maybe 3 or 4 (about what they need to prepare for themselves .eg Skype, headset/microphone etc).

*Offer/product section: A section where the customer can see what services we provide, choose product and click order. When customer click order they will arrive to an order-page (this one you don’t have to design) .
Our products are as followed: Bronze (single coaching session), Silver (small-package), Gold (large-package). Use provided graphics for these products.

*Testimonials section. Currently we have 2 good testimonials, but only with text no portrait picture.

Testimonial1: “Uppiggande och inspirerande! Kommer med enkla vardagstips såväl som svårare tips. Ett roligt sätt att få en spark i baken, så att ekonomi-energin bibehålls! Tack för ett bra samtal!" - Helena Brattvik

Testimonial2: "Värdefullast för mig var kunskapen om alternativa investeringssställen som inte är börs eller eget ägande." - Annika Sjöstedt

*Section with portraits and info about the coaches (currently 2 coaches, but in future will be several, so a design-section that’s lets us add more coaches).

*Footer-section
------------------------------------------------------------------------

Colors:
Use Vardagskompassen (attached file) as colorinspiration. Doesn’t have to be exactly those colors, you can use similar colors if it is more pleasing to the eye and you can also use complementary colors.

Currently we have tried of our own but don't really nail it with any apealing design. This is what we have done so far but we want to replace it with your more professional design:

https://www.harborkite.se/full/Page/coaching13
-------------------------------------------------------------

SUMMARIZE of the above design-description:

* Our logo (attached psd-file with smart-object. You can try different colors with color-overlay)

*Apealing headerimage with portrait (attached file "big_portrait")

*Introduction text (use dummy text about 100 words)

*Text about Vardagskompassen (use dummy text about 200 words)

*Vardagskompassen (attached psd-file with smart-object)

*What we are covering during a coaching session (dummy text about 200 words and about 5 or 6 bullets)

*3-4 Unique Selling Points with stylish number icons (not 2 small) and some text.
*Our offers Bronze, Silver, Gold (attached pictures)
*Testimonials
*Picture & info about coaches (attached pictures, choose whichever suits you)
*Footer

Please comment if there are questions.

Target Market(s)

People who want to learn how to create a richer lifestyle which involves more freedom and a better well-being

Number of Pages Required

1 page

Font styles to use
Sans Serif
Other font styles liked:
• Roboto

Requirements
Should not have
• A cheezy unmodern landingpage with lots of texts and 10 sign-up buttons.
• This page is not a site about capturing emails and building lists by provide a "best-guide-for-something". It´s about getting people to book and pay for one or more coaching-sessions.

```html
<!DOCTYPE html>
<html lang="sv">
<head>
<meta charset="utf-8">
<title>Harbor Kite – Livsstilscoaching</title>
<link rel="stylesheet" href="https://fonts.googleapis.com/css2?family=Open+Sans:wght@400;600;700&display=swap">
<style>
:root{
  --nav:#0f1620;
  --heading:#23496b;
  --text:#777d85;
  --muted:#9aa0a6;
  --light:#eef0f4;
  --paper:#ffffff;
  --soft:#f6f6f6;
  --brown:#9a8170;
  --blue:#1e9ad6;
  --orange:#f0962a;
  --green:#27a55a;
  --bark:#8d7262;
  --gold:#e5a020;
  --footer:#262626;
  --footer-bottom:#1b1b1b;
  --footer-head:#4aa3d8;
  --button:#2f86c0;
}
*{box-sizing:border-box;margin:0;padding:0}
html,body{width:1200px;height:2715px;overflow:hidden}
body{font-family:"Open Sans",Arial,sans-serif;color:var(--text);background:var(--paper);position:relative}
.wrap{width:770px;margin:0 auto;position:relative}
h2{font-weight:600;color:var(--heading);font-size:24px;text-align:center}
.btn{display:inline-block;border:1px solid #c9cdd2;background:#fff;color:#777;font-size:11px;padding:10px 16px}

/* nav */
.site-nav{height:80px;background:var(--nav);display:flex;align-items:center}
.site-nav .wrap{display:flex;justify-content:space-between;align-items:center}
.brand{display:flex;align-items:center;gap:10px;color:#fff}
.brand-mark{width:22px;height:22px;background:#fff}
.brand-name{font-size:24px;letter-spacing:1px;line-height:1}
.brand-sub{font-size:9px;letter-spacing:1px;color:#fff;display:block;text-align:right;margin-top:3px}
.menu{display:flex;gap:24px;list-style:none;font-size:11px;color:#cfd6df}
.menu .active{color:#fff;text-decoration:underline}

/* hero */
.hero{height:304px;position:relative;background:linear-gradient(90deg,#244f82 0%,#6d97c3 35%,#9cbddb 50%,#a9c6df 51%,#d7e6f1 70%,#88aecb 100%)}
.hero-play{position:absolute;left:383px;top:122px}
.hero-copy{position:absolute;left:626px;top:110px}
.hero-title{font-size:23px;font-weight:600;color:#1b4b75}
.hero-btn{margin-top:10px;display:inline-block;background:#fff;color:#555;font-size:15px;padding:9px 14px}

/* intro */
.intro{height:228px;padding-top:42px;text-align:center}
.intro p{font-size:11px;line-height:18px;margin:14px auto 16px;width:770px}

/* compass */
.compass{height:449px;background:var(--light);padding-top:40px}
.compass-body{display:flex;justify-content:space-between;margin-top:38px}
.compass-text{width:362px;font-size:11px;line-height:18px}
.compass-text p+p{margin-top:16px}
.compass-text .btn{margin-top:14px}
.compass-figure{width:275px;height:290px;margin-right:50px;background:linear-gradient(135deg,#5fb7e6 0%,#f4b23a 50%,#8a7766 75%,#39b56a 100%);border-radius:10px;opacity:.85}

/* reasons */
.reasons{height:279px;padding-top:36px}
.reason-list{display:flex;justify-content:space-between;margin-top:28px;padding:0 20px}
.reason{width:170px;text-align:center}
.reason-icon{width:76px;height:76px;border-radius:50%;border:2px solid currentColor;margin:0 auto;display:flex;align-items:center;justify-content:center}
.reason h3{font-size:13px;font-weight:400;margin:14px 0 6px}
.reason p{font-size:9px;line-height:13px;color:var(--muted)}
.c-blue{color:var(--blue)}.c-orange{color:var(--orange)}.c-green{color:var(--green)}.c-bark{color:var(--bark)}

/* session */
.session{height:253px;background:var(--brown);padding-top:26px;color:#fff}
.session h2{color:#fff}
.session-cols{display:flex;justify-content:space-between;margin-top:24px}
.session-col{width:170px}
.session-col ul{list-style:none;margin-top:12px;font-size:9px;line-height:18px}
.session-col li::before{content:"•";margin-right:7px}

/* offers */
.offers{height:417px;padding-top:32px}
.tabs{display:flex;justify-content:center;gap:0;font-size:24px}
.tab{padding:0 12px 6px;border-bottom:2px solid #e3e3e3;color:#9a9a9a}
.tab.current{color:var(--heading);border-bottom:4px solid var(--bark)}
.plans{display:flex;justify-content:space-between;margin-top:74px}
.plan{width:247px;height:207px;background:var(--light);text-align:center;position:relative;padding-top:62px}
.medal{position:absolute;left:50%;top:-50px;margin-left:-47px;width:94px;height:94px;border-radius:50%}
.medal.bronze{background:radial-gradient(circle at 40% 35%,#f0a864,#c8692a)}
.medal.silver{background:radial-gradient(circle at 40% 35%,#f1f1f1,#a9a9a9)}
.medal.goldm{background:radial-gradient(circle at 40% 35%,#fbd76a,#d7981d)}
.plan h3{font-size:18px;font-weight:600}
.plan p{font-size:11px;line-height:19px;margin-top:4px}
.plan .btn{margin-top:14px}

/* testimonials */
.testimonials{height:208px;background:var(--soft);padding-top:32px;position:relative;text-align:center}
.quote{font-size:14px;line-height:24px;width:740px;margin:10px auto 0;color:#777}
.quote-mark{font-size:26px;color:#999;font-family:Georgia,serif;vertical-align:-6px}
.author{margin-top:10px;color:#444;font-size:15px}
.stars{color:#f2b01e;font-size:16px;letter-spacing:2px}
.arrow{position:absolute;top:90px}

/* coaches */
.coaches{height:285px;padding-top:40px}
.coach-list{display:flex;justify-content:center;gap:48px;margin-top:22px}
.coach{width:106px}
.coach-photo{width:106px;height:105px;background:linear-gradient(160deg,#c9c2b8,#6f6a66)}
.coach h3{font-size:12px;font-weight:400;color:#333;margin-top:8px}
.coach p{font-size:8px;color:var(--muted);margin-top:2px}

/* footer */
.site-footer{height:162px;background:var(--footer);padding-top:30px;color:#bbb}
.footer-cols{display:flex}
.footer-cols h4{color:var(--footer-head);font-size:13px;font-weight:400;margin-bottom:8px}
.footer-cols ul{list-style:none;font-size:9px;line-height:19px}
.footer-cols li::before{content:"•";margin-right:6px}
.f-links{width:198px}.f-links .two{display:flex;gap:38px}
.f-contact{width:168px}.f-more{width:157px}
.subscribe{display:flex;margin-top:4px}
.subscribe span{width:160px;height:36px;background:#eee;color:#555;font-size:10px;padding:12px 12px}
.subscribe b{width:88px;height:36px;background:var(--button);color:#fff;font-size:10px;font-weight:400;padding:12px 14px}
.footer-bar{height:50px;background:var(--footer-bottom);color:#aaa;font-size:9px}
.footer-bar .wrap{display:flex;justify-content:space-between;align-items:center;height:50px}
.social{display:flex;gap:18px}
.social i{display:block;width:10px;height:10px;border-radius:50%;background:#aaa}
</style>
</head>
<body>

<header class="site-nav">
  <div class="wrap">
    <div class="brand">
      <span class="brand-mark"></span>
      <div><span class="brand-name">HARBOR KITE</span><span class="brand-sub">LIVSSTILSCOACHING</span></div>
    </div>
    <ul class="menu">
      <li class="active">Home</li><li>Why Us</li><li>Coaching</li><li>Pricing</li><li>Testimonials</li><li>Contact</li>
    </ul>
  </div>
</header>

<section class="hero" role="img" aria-label="Header photo: coins on a blue background beside a portrait of the two coaches">
  <svg class="hero-play" width="54" height="54" viewBox="0 0 54 54">
    <circle cx="27" cy="27" r="24" fill="none" stroke="#fff" stroke-width="3"/>
    <path d="M21 16 L38 27 L21 38 Z" fill="#fff"/>
  </svg>
  <div class="hero-copy">
    <div class="hero-title">How to Get a Richer Lifestyle</div>
    <span class="hero-btn">Get Started Now</span>
  </div>
</section>

<section class="intro">
  <div class="wrap">
    <h2>What We Mean By a Richer Lifestyle</h2>
    <p>Vad som är en rikare livsstil kan skilja sig åt mellan olika människor. Det kan också vara ganska svårt att på egen hand få en bra bild över vad man egentligen menar med detta. Vi har därför tagit fram en enkel modell för att underlätta förståelsen och skapandet av en rikare livsstil. Detta är en modell vi kallar för Vardagskompassen och den består av nedanstående fyra olika delar som representerar varsin livsstil.</p>
    <span class="btn">Read More</span>
  </div>
</section>

<section class="compass">
  <div class="wrap">
    <h2>About Vardagskompassen</h2>
    <div class="compass-body">
      <div class="compass-text">
        <p>Vad som är en rikare livsstil kan skilja sig åt mellan olika människor. Det kan också vara ganska svårt att på egen hand få en bra bild över vad man egentligen menar med detta. Vi har därför tagit fram en enkel modell för att underlätta förståelsen och skapandet av en rikare livsstil. Detta är en modell vi kallar för Vardagskompassen och den består av nedanstående fyra olika delar som representerar varsin livsstil.</p>
        <p>Matrisen är ett resultat av att vi träffat allt fler människor som börjar ifrågasätta den livsstil de lever idag och söka efter andra alternativ. Alternativ som ofta handlar om en kombination av ett högt välmående och hög frihet i livet. Detta alternativ har vi därför valt att i matrisen definiera som en rikare livsstil. Det är en livsstil där du till exempel inte behöver sälja en tredjedel...</p>
        <span class="btn">Read More</span>
      </div>
      <div class="compass-figure" role="img" aria-label="Vardagskompassen illustration: four coloured quadrants for well-being and freedom with axis arrows"></div>
    </div>
  </div>
</section>

<section class="reasons">
  <div class="wrap">
    <h2>Four reasons why choose coaching</h2>
    <div class="reason-list">
      <div class="reason c-blue">
        <div class="reason-icon"><svg width="34" height="28" viewBox="0 0 34 28" fill="currentColor"><circle cx="17" cy="7" r="5"/><circle cx="7" cy="10" r="4"/><circle cx="27" cy="10" r="4"/><path d="M8 27c0-7 4-11 9-11s9 4 9 11z"/><path d="M0 26c0-5 3-8 7-8 2 0 3 1 3 1-2 2-3 5-3 7z"/><path d="M34 26c0-5-3-8-7-8-2 0-3 1-3 1 2 2 3 5 3 7z"/></svg></div>
        <h3>1.Nulla vel bibendum</h3>
        <p>Aliquam sagittis suscipit pulvinar. Nam rhoncus orci sit amet erat malesuada hendrerit.</p>
      </div>
      <div class="reason c-orange">
        <div class="reason-icon"><svg width="32" height="28" viewBox="0 0 32 28" fill="none" stroke="currentColor" stroke-width="2"><rect x="1" y="1" width="30" height="26"/><path d="M8 22V14M13 22V8M18 22V12M23 22V6" stroke-width="3"/></svg></div>
        <h3>2.Pellentesque habitant</h3>
        <p>Aliquam sagittis suscipit pulvinar. Nam rhoncus orci sit amet erat malesuada hendrerit.</p>
      </div>
      <div class="reason c-green">
        <div class="reason-icon"><svg width="36" height="24" viewBox="0 0 36 24" fill="none" stroke="currentColor" stroke-width="2"><rect x="1" y="1" width="34" height="22"/><rect x="5" y="5" width="26" height="14"/><circle cx="18" cy="12" r="4" fill="currentColor"/></svg></div>
        <h3>3.Maecenas aliquet</h3>
        <p>Aliquam sagittis suscipit pulvinar. Nam rhoncus orci sit amet erat malesuada hendrerit.</p>
      </div>
      <div class="reason c-bark">
        <div class="reason-icon"><svg width="32" height="30" viewBox="0 0 32 30" fill="currentColor"><path d="M16 0L32 8H0z"/><rect x="1" y="9" width="30" height="2"/><rect x="4" y="12" width="3" height="12"/><rect x="11" y="12" width="3" height="12"/><rect x="18" y="12" width="3" height="12"/><rect x="25" y="12" width="3" height="12"/><rect x="0" y="25" width="32" height="4"/></svg></div>
        <h3>4.Nullam tincidunt</h3>
        <p>Aliquam sagittis suscipit pulvinar. Nam rhoncus orci sit amet erat malesuada hendrerit.</p>
      </div>
    </div>
  </div>
</section>

<section class="session">
  <div class="wrap">
    <h2>What happens during a typical coaching session</h2>
    <div class="session-cols">
      <div class="session-col">
        <svg width="26" height="26" viewBox="0 0 26 26"><circle cx="13" cy="13" r="12" fill="#fff"/></svg>
        <ul><li>Praesent ac imperdiet</li><li>Sed consequat ornare</li><li>Suspendisse sollicitudin auctor</li><li>Donec sagittis</li><li>Mauris sit amet ex enim</li></ul>
      </div>
      <div class="session-col">
        <svg width="28" height="26" viewBox="0 0 28 26" fill="none" stroke="#fff" stroke-width="3"><path d="M3 18v-4a11 11 0 0 1 22 0v4"/><rect x="2" y="15" width="6" height="9" rx="2" fill="#fff"/><rect x="20" y="15" width="6" height="9" rx="2" fill="#fff"/></svg>
        <ul><li>Praesent ac imperdiet</li><li>Sed consequat ornare</li><li>Suspendisse sollicitudin auctor</li><li>Donec sagittis</li><li>Mauris sit amet ex enim</li></ul>
      </div>
      <div class="session-col">
        <svg width="30" height="24" viewBox="0 0 30 24"><rect x="1" y="2" width="28" height="20" rx="5" fill="#fff"/></svg>
        <ul><li>Praesent ac imperdiet</li><li>Sed consequat ornare</li><li>Suspendisse sollicitudin auctor</li><li>Donec sagittis</li><li>Mauris sit amet ex enim</li></ul>
      </div>
      <div class="session-col">
        <svg width="26" height="26" viewBox="0 0 26 26" fill="none" stroke="#fff" stroke-width="2"><circle cx="13" cy="13" r="11"/><path d="M2 13h22M13 2c-5 6-5 16 0 22M13 2c5 6 5 16 0 22"/></svg>
        <ul><li>Praesent ac imperdiet</li><li>Sed consequat ornare</li><li>Suspendisse sollicitudin auctor</li><li>Donec sagittis</li><li>Mauris sit amet ex enim</li></ul>
      </div>
    </div>
  </div>
</section>

<section class="offers">
  <div class="wrap">
    <div class="tabs"><span class="tab">Offers</span><span class="tab current">Products</span></div>
    <div class="plans">
      <div class="plan">
        <div class="medal bronze" role="img" aria-label="Bronze product medal"></div>
        <h3 class="c-blue">Engångsession</h3>
        <p>Inkluderar 1 session<br>Pris 650 SEK</p>
        <span class="btn">Book Now</span>
      </div>
      <div class="plan">
        <div class="medal silver" role="img" aria-label="Silver product medal"></div>
        <h3 class="c-green">Silverpaketet</h3>
        <p>Inkluderar 5 sessioner<br>Pris 3050 SEK</p>
        <span class="btn">Book Now</span>
      </div>
      <div class="plan">
        <div class="medal goldm" role="img" aria-label="Gold product medal"></div>
        <h3 class="c-orange">Guldpaketet</h3>
        <p>Inkluderar 10 sessioner<br>Pris 5800 SEK</p>
        <span class="btn">Book Now</span>
      </div>
    </div>
  </div>
</section>

<section class="testimonials">
  <h2>Testimonials</h2>
  <svg class="arrow" style="left:24px" width="14" height="24" viewBox="0 0 14 24" fill="none" stroke="#999" stroke-width="2"><path d="M12 2L2 12l10 10"/></svg>
  <svg class="arrow" style="right:24px" width="14" height="24" viewBox="0 0 14 24" fill="none" stroke="#999" stroke-width="2"><path d="M2 2l10 10L2 22"/></svg>
  <p class="quote"><span class="quote-mark">“</span> Uppiggande och inspirerande! Kommer med enkla vardagstips såväl som svårare tips. Ett roligt sätt att få en spark i baken, så att ekonomi-energin bibehålls! Tack för ett bra samtal! <span class="quote-mark">”</span></p>
  <p class="author">Helena Brattvik</p>
  <p class="stars">★★★★★</p>
</section>

<section class="coaches">
  <h2>Coaches</h2>
  <div class="coach-list">
    <div class="coach"><div class="coach-photo" role="img" aria-label="Portrait photo of coach Anders"></div><h3>coach_anders</h3><p>Mauris quis sodales</p></div>
    <div class="coach"><div class="coach-photo" role="img" aria-label="Portrait photo of coach Joakim"></div><h3>coach_joakim</h3><p>Mauris quis sodales</p></div>
    <div class="coach"><div class="coach-photo" role="img" aria-label="Portrait photo of a coach"></div><h3>Erik Lindqvist</h3><p>Mauris quis sodales</p></div>
    <div class="coach"><div class="coach-photo" role="img" aria-label="Portrait photo of a coach"></div><h3>Erik Lindqvist</h3><p>Mauris quis sodales</p></div>
  </div>
</section>

<footer>
  <div class="site-footer">
    <div class="wrap footer-cols">
      <div class="f-links"><h4>LINKS</h4>
        <div class="two"><ul><li>Home</li><li>Why Us</li><li>Coaching</li><li>Pricing</li></ul><ul><li>Testimonials</li><li>Contact</li></ul></div>
      </div>
      <div class="f-contact"><h4>CONTACT</h4>
        <ul><li>Phone : 046 555 0182</li><li>Email : info@anders-coach.se</li><li>Email : info@joakim-coach.se</li><li>Live Chat With Us</li></ul>
      </div>
      <div class="f-more"><h4>MORE LINKS</h4>
        <ul><li>Terms and conditions</li><li>Privacy Policy</li><li>Sitemap</li></ul>
      </div>
      <div class="f-news"><h4>NEWSLETTER SUBSCRIBE</h4>
        <div class="subscribe"><span>Email Address</span><b>SUBSCRIBE</b></div>
      </div>
    </div>
  </div>
  <div class="footer-bar">
    <div class="wrap">
      <span>Copyright © 2016 Harbor Kite. All rights reserved.</span>
      <div class="social"><i></i><i></i><i></i></div>
    </div>
  </div>
</footer>

</body>
</html>
```